Business cards in digital learning for freelancer

Hello, I need a business cards in french. I work in the Digital learning industries as freeelancer; I'm an expert in digital learning. I work in France. My customer are in the health industry, pharmaceutical industry, and training organization. I've got a logo. I offer three services: consulting, Design, and Training. In the consulting, I offers coaching to choose your digital learning tools and the digital learning strategy. For the Design, I product differents level of elearning like rapid-learning, elearning, micro-learning, video-learning. And for the training service, I've create training about pedagogy, digital learning management project, Digital learning design.
I join my Logo create in this platform. My universe is gamified. I like the life, and I'm very social. I want a card like I'm I. I love Art (painting), Europeen comics. I use in my visual support "permanent maker" font and caracters. I would like cards: elegant, modern, Top class. If you need any information, you can ask me.
thanks for ideas

Target Market(s)

in health industries and training organization for Training manager, instructor, human resources director

Contact Information for Business Card

Phone number : 06 71 38 95 14 , mail: bastiengolmier@quelmoto.fr, web: bastiengolmier.fr , Carrivo

Font styles to use
Sans Serif

Requirements
Must have
• Use my logo and write my 3 services (consulting, training, design)

```html
<!DOCTYPE html>
<html lang="fr">
<head>
<meta charset="utf-8">
<title>Bastien Golmier – Carte de visite</title>
<link rel="stylesheet" href="https://fonts.googleapis.com/css2?family=Josefin+Sans:wght@300;400;700&family=Cinzel:wght@400;500&display=swap">
<style>
  :root {
    --page-bg: #dfe5ec;
    --card-bg: #f4f5f6;
    --brand-orange: #d9531e;
    --band-orange: #c84d1d;
    --band-orange-deep: #a83d14;
    --band-dark: #3a3b3e;
    --ink-dark: #3d3d3f;
    --ink-light: #f6e6dc;
    --ink-soft: #f0cdb8;
  }
  * { margin: 0; padding: 0; box-sizing: border-box; }
  html, body { width: 1200px; height: 894px; overflow: hidden; }
  body { background: var(--page-bg); position: relative; font-family: "Josefin Sans", sans-serif; }

  .business-card {
    position: absolute; left: 100px; top: 163px;
    width: 1000px; height: 568px;
    background: var(--card-bg);
    border-radius: 44px;
    overflow: hidden;
    box-shadow: 0 18px 40px rgba(40, 55, 75, 0.18);
  }

  .brand-block {
    position: absolute; left: 35px; top: 30px; width: 330px;
    text-align: center;
  }
  .brand-mark {
    display: block; margin: 0 auto 14px;
    width: 130px; height: 130px;
    border: 14px solid var(--brand-orange);
    border-radius: 50%;
  }
  .brand-name {
    font-family: "Josefin Sans", sans-serif;
    font-weight: 700; font-size: 40px; letter-spacing: 2px;
    color: var(--brand-orange); line-height: 1;
  }
  .brand-field {
    display: flex; align-items: center; gap: 6px;
    margin-top: 10px;
    font-family: "Cinzel", serif; font-size: 19px; color: var(--ink-dark);
  }
  .brand-field::before, .brand-field::after {
    content: ""; flex: 1; height: 1.5px; background: var(--ink-dark);
  }
  .brand-services {
    margin-top: 6px;
    font-family: "Cinzel", serif; font-size: 18px; color: var(--ink-dark);
    letter-spacing: 0.5px; white-space: nowrap;
  }

  .contact-band {
    position: absolute; left: 0; top: 319px; width: 1000px; height: 213px;
    background: linear-gradient(100deg, var(--band-orange) 0%, var(--band-orange-deep) 55%, var(--band-orange) 82%);
  }
  .contact-band .dark-edge {
    position: absolute; right: 0; top: 0; width: 140px; height: 100%;
    background: var(--band-dark);
  }
  .band-brand {
    position: absolute; right: 40px; top: 30px;
    display: flex; flex-direction: column; align-items: center; gap: 12px;
  }
  .band-brand .band-ring {
    width: 110px; height: 110px; border-radius: 50%;
    border: 16px solid var(--brand-orange);
  }
  .band-brand .band-name {
    font-weight: 700; font-size: 22px; letter-spacing: 2px; color: var(--ink-light);
  }

  .person { position: absolute; left: 35px; top: 18px; color: var(--ink-light); }
  .person-name { font-size: 31px; font-weight: 400; letter-spacing: 1px; }
  .person-role { font-size: 22px; font-weight: 300; letter-spacing: 1px; color: var(--ink-soft); margin-top: 6px; }

  .contact-list { position: absolute; left: 35px; top: 104px; list-style: none; color: var(--ink-soft); }
  .contact-list li {
    display: flex; align-items: center; gap: 12px;
    font-size: 22px; font-weight: 300; letter-spacing: 0.5px; height: 34px;
  }
  .contact-list svg { width: 22px; height: 22px; flex: none; }
  .contact-list .social { margin-left: 26px; display: inline-flex; align-items: center; gap: 12px; }
  .contact-list .social-dot { width: 18px; height: 18px; border-radius: 50%; background: var(--ink-soft); }
</style>
</head>
<body>
  <section class="business-card" aria-label="Carte de visite Bastien Golmier">
    <header class="brand-block">
      <span class="brand-mark" aria-hidden="true"></span>
      <div class="brand-name">GOLMIER</div>
      <div class="brand-field">Digital Learning</div>
      <div class="brand-services">Consulting, Training, Design</div>
    </header>

    <div class="contact-band">
      <div class="dark-edge"></div>
      <div class="band-brand" aria-hidden="true">
        <span class="band-ring"></span>
        <span class="band-name">GOLMIER</span>
      </div>

      <div class="person">
        <div class="person-name">Bastien Golmier</div>
        <div class="person-role">Digital Learning consultant</div>
      </div>

      <ul class="contact-list">
        <li>
          <svg viewBox="0 0 24 24" aria-hidden="true"><circle cx="12" cy="12" r="11" fill="none" stroke="currentColor" stroke-width="1.8"/><path d="M7 9c0-1.5 2.5-2.5 5-2.5S17 7.5 17 9l-2 1-1-1.5h-4L9 10 7 9zm2 2h6l1.5 5h-9z" fill="currentColor"/></svg>
          06 71 38 95 14
        </li>
        <li>
          <svg viewBox="0 0 24 24" aria-hidden="true"><circle cx="12" cy="12" r="11" fill="none" stroke="currentColor" stroke-width="1.8"/><rect x="6.5" y="8" width="11" height="8" rx="1" fill="none" stroke="currentColor" stroke-width="1.6"/><path d="M6.5 8.5 12 12.5l5.5-4" fill="none" stroke="currentColor" stroke-width="1.6"/></svg>
          bastiengolmier@quelmoto.fr
        </li>
        <li>
          <svg viewBox="0 0 24 24" aria-hidden="true"><circle cx="12" cy="12" r="11" fill="none" stroke="currentColor" stroke-width="1.8"/><ellipse cx="12" cy="12" rx="4" ry="8" fill="none" stroke="currentColor" stroke-width="1.4"/><path d="M4 12h16" stroke="currentColor" stroke-width="1.4"/></svg>
          bastiengolmier.fr
          <span class="social"><span class="social-dot" aria-hidden="true"></span>Carrivo /bastien-golmier-elearning</span>
        </li>
      </ul>
    </div>
  </section>
</body>
</html>
```